Northfield Builders Guild Business card

We are looking for a new business card design with photo included.
Our business is a nonprofit construction contractor membership organization. We offer business education, assist with business setup and licensing, provide safety training, and provide a member directory.
URL: www.builderslinkguild.org
Color code:
CMYK: 0 cyan, 42 magenta, 100 yellow, 0 black for Print.
Hexidecimal: #FF9900
RGB: R 255; G 153; B 0

```html
<!DOCTYPE html>
<html lang="en">
<head>
<meta charset="utf-8">
<title>Northfield Builders Guild — Business Card</title>
<link href="https://fonts.googleapis.com/css2?family=Jost:wght@400;500;700;800&display=swap" rel="stylesheet">
<style>
  :root {
    --stage: #2b2b2b;
    --card-white: #ffffff;
    --card-black: #1a1a1a;
    --ink: #2e2e30;
    --ink-soft: #555558;
    --orange: #ff9900;
    --deboss: #2c2c2d;
    --rule: #8a8a8a;
  }
  * { margin: 0; padding: 0; box-sizing: border-box; }
  html, body { width: 1200px; height: 768px; overflow: hidden; }
  body {
    background: var(--stage);
    font-family: "Jost", "Futura", sans-serif;
    display: flex;
    align-items: center;
    justify-content: center;
    gap: 40px;
  }
  .card {
    position: relative;
    width: 540px;
    height: 308px;
    overflow: hidden;
  }
  /* Back */
  .card--back {
    background: var(--card-black);
    display: flex;
    align-items: center;
    justify-content: center;
  }
  .back-name {
    color: var(--deboss);
    font-weight: 800;
    font-size: 40px;
    line-height: 1;
    text-transform: uppercase;
    text-align: center;
    letter-spacing: 0.5px;
  }
  /* Front */
  .card--front { background: var(--card-white); }
  .card-bands { position: absolute; inset: 0; width: 100%; height: 100%; }
  .brand {
    position: absolute;
    left: 36px;
    top: 96px;
    width: 220px;
    color: var(--ink);
    font-weight: 800;
    font-size: 30px;
    line-height: 1;
    text-transform: uppercase;
  }
  .divider {
    position: absolute;
    left: 272px;
    top: 78px;
    width: 1px;
    height: 150px;
    background: var(--rule);
  }
  .details {
    position: absolute;
    left: 292px;
    top: 76px;
    color: var(--ink-soft);
    font-size: 13.5px;
    line-height: 1.3;
  }
  .person-name {
    color: var(--ink);
    font-weight: 800;
    font-size: 19px;
    letter-spacing: 1px;
    text-transform: uppercase;
    line-height: 1.1;
  }
  .person-title {
    color: var(--orange);
    font-size: 12px;
    text-transform: uppercase;
    letter-spacing: 0.5px;
    margin-bottom: 8px;
  }
  .address { margin-bottom: 8px; }
  .contact-row { display: flex; align-items: center; gap: 7px; }
  .contact-row svg { width: 11px; height: 11px; fill: var(--orange); flex: none; }
  .website {
    position: absolute;
    right: 34px;
    bottom: 13px;
    color: var(--card-white);
    font-size: 15px;
    letter-spacing: 0.3px;
  }
</style>
</head>
<body>

  <section class="card card--back" aria-label="Business card back">
    <p class="back-name">Northfield<br>Builders<br>Guild</p>
  </section>

  <section class="card card--front" aria-label="Business card front">
    <svg class="card-bands" viewBox="0 0 540 308" preserveAspectRatio="none" aria-hidden="true">
      <polygon points="0,280 334,280 326,294 0,294" fill="#2e2e30"/>
      <polygon points="0,294 326,294 344,254 540,254 540,308 0,308" fill="#ff9900"/>
    </svg>

    <p class="brand">Northfield<br>Builders<br>Guild</p>

    <div class="divider"></div>

    <div class="details">
      <p class="person-name">Daniel Hart</p>
      <p class="person-title">President</p>
      <p class="address">4200 NW Alder Ave.,<br>Suite #210<br>Salem, OR 97301</p>
      <p class="contact-row">
        <svg viewBox="0 0 24 24" aria-hidden="true"><path d="M6.6 10.8a15.1 15.1 0 0 0 6.6 6.6l2.2-2.2a1 1 0 0 1 1-.25 11.4 11.4 0 0 0 3.6.57 1 1 0 0 1 1 1V20a1 1 0 0 1-1 1A17 17 0 0 1 3 4a1 1 0 0 1 1-1h3.5a1 1 0 0 1 1 1c0 1.25.2 2.45.57 3.57a1 1 0 0 1-.25 1z"/></svg>
        (541) 555-0147
      </p>
      <p class="contact-row">
        <svg viewBox="0 0 24 24" aria-hidden="true"><path d="M7 1h10a2 2 0 0 1 2 2v18a2 2 0 0 1-2 2H7a2 2 0 0 1-2-2V3a2 2 0 0 1 2-2zm0 3v15h10V4z"/></svg>
        541.555.0193
      </p>
      <p class="contact-row">
        <svg viewBox="0 0 24 24" aria-hidden="true"><path d="M2 5h20v14H2zm2 2v.5l8 5 8-5V7z"/></svg>
        help@nbguild.org
      </p>
    </div>

    <p class="website">www.builderslinkguild.org</p>
  </section>

</body>
</html>
```